Business Card Design For Office Furniture Clearance Company

Kestrel Office Clearance - our company name pretty much explains what we do, we clear offices for high end clients, mainly plc's and large international companies.

We require a nice looking business card that displays professionalism but without being too serious.

It would be nice to see just a little more than a conventional boring business card, make sure you add some flare.

Industry/Entity Type

Office Furniture

Contact Information for Business Card

CARD 1

Mark Holloway
Director
mark@kestrelofficeclearance.co.uk
m: 07700 153928

t: 01632 960418
www.kestrelofficeclearance.co.uk

Kestrel Office Clearance
Unit K4 B
2-8 Fenwick Lane
Harlow Vale
Brackenford
ZZ9 4QT

free office clearances… you cant get better than that.

CARD 2

Peter Radford
Director
peter@kestrelofficeclearance.co.uk
m: 07700 382615

t: 01632 960418

Kestrel Office Clearance
Unit K4 B
2-8 Fenwick Lane
Harlow Vale
Brackenford
ZZ9 4QT

Font styles to use
Sans Serif

Requirements
Must have
• A white background - as we have a blue logo.
Nice to have
• Nice use of the logo - play around with this and dissect it.

```html
<!DOCTYPE html>
<html lang="en">
<head>
<meta charset="utf-8">
<title>Kestrel Office Clearance – Business Cards</title>
<link rel="stylesheet" href="https://fonts.googleapis.com/css2?family=Arimo:wght@400;700&display=swap">
<style>
  :root {
    --page-bg: #e9e7e3;
    --brand-blue: #1b8bd2;
    --brand-blue-deep: #1277b8;
    --card-dark: #4b4b4b;
    --card-dark-edge: #3c3c3c;
    --paper: #ffffff;
    --ink-grey: #5a5a5a;
    --text-light: #ffffff;
  }
  * { box-sizing: border-box; margin: 0; padding: 0; }
  html, body { width: 1200px; height: 950px; overflow: hidden; }
  body {
    background: var(--page-bg);
    font-family: "Arimo", Arial, sans-serif;
    position: relative;
  }
  .card {
    position: absolute;
    width: 700px;
    height: 400px;
    border-radius: 4px;
    overflow: hidden;
    box-shadow: 0 10px 28px rgba(0,0,0,0.18);
  }

  /* Back of card */
  .card-back {
    left: 150px; top: 60px;
    background: linear-gradient(160deg, var(--card-dark) 0%, var(--card-dark-edge) 100%);
  }
  .card-back .brand-disc {
    position: absolute;
    left: 255px; top: 65px;
    width: 190px; height: 190px;
    border-radius: 50%;
    background: var(--paper);
    display: flex; align-items: center; justify-content: center;
    font-weight: 700; font-size: 34px;
    color: var(--card-dark);
  }
  .card-back .tagline {
    position: absolute;
    left: 0; right: 0; top: 310px;
    text-align: center;
    color: var(--text-light);
    font-size: 17px;
    letter-spacing: 0.3px;
  }

  /* Front of card */
  .card-front {
    left: 350px; top: 490px;
    background: var(--paper);
  }
  .card-front .wave { position: absolute; inset: 0; }
  .card-front .brand-disc {
    position: absolute;
    left: 50px; top: 58px;
    width: 175px; height: 175px;
    border-radius: 50%;
    background: var(--brand-blue);
    display: flex; align-items: center; justify-content: center;
    font-weight: 700; font-size: 32px;
    color: var(--text-light);
  }
  .holder {
    position: absolute;
    right: 32px; top: 26px;
    text-align: right;
  }
  .holder-name {
    font-weight: 700; font-size: 28px;
    color: var(--brand-blue);
  }
  .holder-role {
    font-size: 17px;
    color: var(--ink-grey);
    margin-top: 4px;
  }
  .address {
    position: absolute;
    right: 32px; top: 212px;
    text-align: right;
    color: var(--text-light);
    font-size: 17px;
    line-height: 23px;
    font-style: normal;
  }
  .address .company { font-weight: 700; }
  .contacts {
    position: absolute;
    left: 30px; bottom: 18px;
    list-style: none;
    color: var(--text-light);
    font-size: 16px;
    line-height: 25px;
  }
  .contacts li { display: flex; align-items: center; gap: 9px; }
  .contacts svg { width: 15px; height: 15px; flex: none; }
</style>
</head>
<body>

<section class="card card-back" aria-label="Business card, back">
  <div class="brand-disc">Kestrel</div>
  <p class="tagline">Clear desks, clear floors… we handle the heavy lifting.</p>
</section>

<section class="card card-front" aria-label="Business card, front">
  <svg class="wave" viewBox="0 0 700 400" preserveAspectRatio="none" aria-hidden="true">
    <path d="M0 265 C 250 225, 480 185, 700 100 L700 400 L0 400 Z" fill="var(--brand-blue)"/>
    <path d="M0 265 C 250 225, 480 185, 700 100 L700 160 C 480 235, 250 260, 0 285 Z" fill="var(--brand-blue-deep)" opacity="0.35"/>
    <path d="M0 250 C 250 210, 480 170, 700 86" fill="none" stroke="var(--brand-blue)" stroke-width="2"/>
  </svg>

  <div class="brand-disc">Kestrel</div>

  <div class="holder">
    <p class="holder-name">Mark Holloway</p>
    <p class="holder-role">Director</p>
  </div>

  <address class="address">
    <p class="company">Kestrel Office Clearance</p>
    <p>Unit K4 B, 2-8 Fenwick Lane</p>
    <p>Harlow Vale, Brackenford</p>
    <p>ZZ9 4QT</p>
  </address>

  <ul class="contacts">
    <li>
      <svg viewBox="0 0 16 16" aria-hidden="true"><path fill="#fff" d="M3 1h3l1.5 4-2 1.3a9 9 0 0 0 4.2 4.2L11 8.5l4 1.5v3c0 1-1 2-2 2A12 12 0 0 1 1 3c0-1 1-2 2-2z"/></svg>
      01632 960418
    </li>
    <li>
      <svg viewBox="0 0 16 16" aria-hidden="true"><rect x="4" y="1" width="8" height="14" rx="1.5" fill="none" stroke="#fff" stroke-width="1.6"/><circle cx="8" cy="12.5" r="0.9" fill="#fff"/></svg>
      07700 153928
    </li>
    <li>
      <svg viewBox="0 0 16 16" aria-hidden="true"><rect x="1" y="3" width="14" height="10" rx="1" fill="#fff"/><path d="M1.5 3.5 8 9l6.5-5.5" fill="none" stroke="var(--brand-blue)" stroke-width="1.3"/></svg>
      mark@kestrelofficeclearance.co.uk
    </li>
    <li>
      <svg viewBox="0 0 16 16" aria-hidden="true"><circle cx="8" cy="8" r="6.5" fill="none" stroke="#fff" stroke-width="1.5"/><path d="M1.5 8h13M8 1.5c-3 3.5-3 9.5 0 13M8 1.5c3 3.5 3 9.5 0 13" fill="none" stroke="#fff" stroke-width="1.1"/></svg>
      www.kestrelofficeclearance.co.uk
    </li>
  </ul>
</section>

</body>
</html>
```